New Bicycle shop business card

Hi!
I'm looking for a business card for my new proffesional bike mechanics shop. This shop is only for fixing broken bikes and not selling bikes.
Peferbly a modern and sleek and modern design.
Colors: black, grey, red, white
Information:
Name: Rijwielwerkplaats Vanhoutte
Shop owner: Bart Vanhoutte & Marieke Segers
Website: www.rijwielwerkplaats-vanhoutte.be
Email: info@rijwielwerkplaats-vanhoutte.be
Phone number: +32471902368
Street adres: Kerkweg 46
9940 Bellebeke
Slogan/shop information: Herstellingen van alle merken.
Logo: see files.
Target Market(s)
People who seek a mechanic to fix or upgrade their bikes.
Contact Information for Business Card
Information:
Website: info@rijwielwerkplaats-vanhoutte.be
9940 Bellebeke
Logo: see files.

```html
<!DOCTYPE html>
<html lang="nl">
<head>
<meta charset="utf-8">
<title>Rijwielwerkplaats Vanhoutte – visitekaartje</title>
<link rel="stylesheet" href="https://fonts.googleapis.com/css2?family=Roboto:wght@400;700&family=Michroma&display=swap">
<style>
  :root {
    --backdrop: #3a3a3c;
    --card-black: #1c1c1e;
    --brand-red: #df2b3c;
    --band-grey: #9b9ea3;
    --ink-white: #ffffff;
    --ink-soft: #d9d9dc;
  }
  * { box-sizing: border-box; margin: 0; padding: 0; }
  html, body { width: 799px; height: 1200px; overflow: hidden; }
  body {
    background: var(--backdrop);
    font-family: "Roboto", Arial, sans-serif;
    display: flex; flex-direction: column; align-items: center; justify-content: space-around;
    padding: 60px 0;
  }
  .card {
    position: relative; width: 640px; height: 366px; border-radius: 24px;
    overflow: hidden; background: var(--card-black);
    box-shadow: 0 14px 30px rgba(0,0,0,.45);
  }
  /* front */
  .card-front { display: flex; flex-direction: column; align-items: center; justify-content: center; }
  .brand {
    display: flex; align-items: center; gap: 14px;
    color: var(--ink-white); font-weight: 700; font-size: 30px; line-height: 1.1;
    text-transform: uppercase; letter-spacing: 1px;
  }
  .brand-mark { width: 30px; height: 30px; background: var(--brand-red); flex: none; }
  .brand-name { display: block; }
  .front-url { margin-top: 40px; color: var(--ink-soft); font-size: 17px; }
  .front-url .accent { color: var(--brand-red); }
  /* back */
  .card-back { background: var(--brand-red); }
  .back-shape { position: absolute; inset: 0; }
  .back-brand {
    position: absolute; left: 34px; top: 112px; width: 250px;
  }
  .back-brand .brand { font-size: 21px; gap: 10px; }
  .back-brand .brand-mark { width: 22px; height: 22px; }
  .tagline { margin-top: 14px; color: var(--ink-white); font-size: 14px; }
  .contact {
    position: absolute; left: 330px; top: 88px; width: 300px; color: var(--ink-white);
  }
  .person-name { font-family: "Michroma", "Roboto", sans-serif; font-size: 19px; text-transform: uppercase; }
  .person-role { font-size: 14px; margin-top: 2px; }
  .contact-list { list-style: none; margin-top: 20px; }
  .contact-list li { display: flex; align-items: center; gap: 10px; font-size: 14.5px; margin-bottom: 6px; white-space: nowrap; }
  .contact-list svg { width: 14px; height: 14px; flex: none; }
  .address { margin-top: 10px; font-size: 15px; line-height: 1.35; }
</style>
</head>
<body>

<section class="card card-front" aria-label="Voorkant">
  <div class="brand">
    <span class="brand-mark"></span>
    <span class="brand-name">Rijwielwerkplaats<br>Vanhoutte</span>
  </div>
  <p class="front-url">www.rijwielwerkplaats-<span class="accent">vanhoutte</span>.be</p>
</section>

<section class="card card-back" aria-label="Achterkant">
  <svg class="back-shape" viewBox="0 0 640 366" preserveAspectRatio="none" aria-hidden="true">
    <path d="M0 0 H322 C360 120 330 270 206 366 H0 Z" fill="var(--band-grey)"/>
    <path d="M0 0 H304 C340 120 310 265 184 366 H0 Z" fill="var(--card-black)"/>
  </svg>

  <div class="back-brand">
    <div class="brand">
      <span class="brand-mark"></span>
      <span class="brand-name">Rijwielwerkplaats<br>Vanhoutte</span>
    </div>
    <p class="tagline">Herstellingen van alle merken</p>
  </div>

  <div class="contact">
    <h2 class="person-name">Marieke Segers</h2>
    <p class="person-role">Owner</p>
    <ul class="contact-list">
      <li>
        <svg viewBox="0 0 24 24" fill="currentColor"><path d="M6.6 10.8a15 15 0 0 0 6.6 6.6l2.2-2.2c.3-.3.7-.4 1-.2 1.1.4 2.3.6 3.6.6.6 0 1 .4 1 1V20c0 .6-.4 1-1 1A17 17 0 0 1 3 4c0-.6.4-1 1-1h3.5c.6 0 1 .4 1 1 0 1.3.2 2.5.6 3.6.1.3 0 .7-.2 1z"/></svg>
        +32471902368
      </li>
      <li>
        <svg viewBox="0 0 24 24" fill="none" stroke="currentColor" stroke-width="2"><circle cx="12" cy="12" r="9"/><path d="M3 12h18M12 3c3 3 3 15 0 18M12 3c-3 3-3 15 0 18"/></svg>
        www.rijwielwerkplaats-vanhoutte.be
      </li>
      <li>
        <svg viewBox="0 0 24 24" fill="currentColor"><path d="M2 5h20v14H2z" fill="none" stroke="currentColor" stroke-width="2"/><path d="M2 5l10 8 10-8" fill="none" stroke="currentColor" stroke-width="2"/></svg>
        info@rijwielwerkplaats-vanhoutte.be
      </li>
    </ul>
    <p class="address">Kerkweg 46<br>9940 Bellebeke</p>
  </div>
</section>

</body>
</html>
```